Need help in designing new business card utilizing our new logo.

BuildMark Solutions works with Construction Business Owners, Managers & IT Professionals to strengthen software usage and increase user productivity.

Our Construction Accounting and Mobile Field Management Software Clients engage with us in the following areas:

New Software Implementations
Software Re-Implementations
Redesigning Software Usage at the User Level
Project Coordination & Management
Continued Software Support

Old tag line:
Weighing Options - Implementing Solutions

www.buildmark-solutions.example

Ridge 4 is a product, but not needed for a new business card.

```html
<!DOCTYPE html>
<html lang="en">
<head>
<meta charset="utf-8">
<title>BuildMark Solutions – Business Card</title>
<link href="https://fonts.googleapis.com/css2?family=Arimo:wght@400;700&display=swap" rel="stylesheet">
<style>
  :root {
    --page-bg: #e8e5df;
    --brand-blue: #3441c2;
    --brand-blue-deep: #2a34a6;
    --card-white: #f5f5f5;
    --stripe-grey: #c9c9cb;
    --text-grey: #8a8a90;
    --text-light: #ffffff;
  }
  * { margin: 0; padding: 0; box-sizing: border-box; }
  html, body {
    width: 1200px; height: 780px; overflow: hidden;
    background: var(--page-bg);
    font-family: "Arimo", Arial, sans-serif;
  }
  .sheet {
    width: 1200px; height: 780px;
    display: flex; align-items: center; justify-content: center; gap: 40px;
  }
  .card {
    position: relative;
    width: 540px; height: 309px;
    overflow: hidden;
    box-shadow: 0 6px 18px rgba(0,0,0,.18);
  }

  /* Front */
  .card-front { background: var(--card-white); }
  .front-top { position: absolute; inset: 0 0 auto 0; height: 168px; }
  .front-stripe { position: absolute; left: 0; right: 0; top: 168px; height: 10px; background: var(--stripe-grey); }
  .front-band {
    position: absolute; left: 0; right: 0; top: 178px; bottom: 0;
    background: linear-gradient(135deg, var(--brand-blue) 0%, var(--brand-blue-deep) 100%);
    color: var(--text-light);
  }
  .brand-name {
    position: absolute; left: 32px; top: 86px;
    display: flex; align-items: center; gap: 12px;
    font-weight: 700; font-size: 28px; color: var(--brand-blue);
  }
  .brand-square { width: 26px; height: 26px; background: var(--brand-blue); }
  .person { position: absolute; right: 30px; top: 26px; text-align: right; }
  .person-name { font-weight: 700; font-size: 17px; color: var(--brand-blue); }
  .person-role { font-size: 12px; color: var(--text-grey); margin-top: 2px; }
  .contact-list {
    position: absolute; left: 32px; bottom: 24px;
    list-style: none; font-size: 12.5px; line-height: 1.45;
  }
  .address {
    position: absolute; right: 30px; top: 22px;
    font-style: normal; font-size: 12.5px; line-height: 1.45; text-align: left;
  }

  /* Back */
  .card-back {
    background: linear-gradient(160deg, #3b48cc 0%, var(--brand-blue) 45%, var(--brand-blue-deep) 100%);
    color: var(--text-light);
  }
  .back-brand {
    position: absolute; right: 34px; top: 38px;
    display: flex; align-items: center; gap: 12px;
    font-weight: 700; font-size: 26px; color: var(--text-light);
  }
  .back-brand .brand-square { background: var(--text-light); width: 24px; height: 24px; }
  .service-list {
    position: absolute; left: 34px; top: 128px;
    list-style: none; font-size: 13px; line-height: 1.75;
  }
  .service-list li { display: flex; align-items: center; gap: 9px; }
  .service-bullet { width: 8px; height: 8px; background: var(--text-light); flex: none; }
</style>
</head>
<body>
<main class="sheet">

  <section class="card card-front" aria-label="Business card front">
    <div class="front-top">
      <div class="brand-name"><span class="brand-square"></span>BuildMark Solutions</div>
      <div class="person">
        <div class="person-name">Dana R. Whitlock</div>
        <div class="person-role">Owner</div>
      </div>
    </div>
    <div class="front-stripe"></div>
    <div class="front-band">
      <address class="address">
        48 Harbor Lane<br>
        Suite 112<br>
        Millbrook NY 12545
      </address>
      <ul class="contact-list">
        <li>O: 555-014-2200 ext.100</li>
        <li>C: 555-014-7731</li>
        <li>E: dana.whitlock@buildmark-solutions.example</li>
      </ul>
    </div>
  </section>

  <section class="card card-back" aria-label="Business card back">
    <div class="back-brand"><span class="brand-square"></span>BuildMark Solutions</div>
    <ul class="service-list">
      <li><span class="service-bullet"></span>New Software Implementations</li>
      <li><span class="service-bullet"></span>Software Re-Implementations</li>
      <li><span class="service-bullet"></span>Redesigning Software Usage at the User Level</li>
      <li><span class="service-bullet"></span>Project Coordination &amp; Management</li>
      <li><span class="service-bullet"></span>Continued Software Support</li>
    </ul>
  </section>

</main>
</body>
</html>
```